A start-up named "Corvane Therapeutics" - needs a new PowerPoint design

We need a new PowerPoint Design for an early-stage start-up named "Corvane Therapeutics" seeking to disrupt the current approach towards drug discovery within aging disorders.

We would like to build on Corvane's legacy, the founder of the modern science of genetics, by employing a multidisciplinary approach, experimenting, and providing elderly patients the attention they deserve.

We have selected the suffix "therapeutics" intentionally as it stands for (a medicine) the treatment of disease; the science of healing. Alzheimer’s treatment is a huge, urgent, unmet need:
- Shift from a disease-management system to a preventive medicine system
- Focus on increasing the health span, not only the life span

Target Market(s)

Pharma/ Biotech Executives Medical Institutions Healthcare professionals (MDs, nurses, payors, pharmacists, etc.) Patients

Industry/Entity Type

Healthcare

Other font styles liked:
• Celias

Colors
0054AA
0677BA
7BADD7
CADEEF
E8F1F8
E54698
E96AAD
F1A4CE
F9D9EA
FCEFF6
A7469A
B969AE
D3A5CF
EDDBEB
F8F0F9
6B429C
8869AF
B7A5CE
E3DAEB
F3F0F8

Requirements
Must have
• - differentiate from other companies named after Corvane - differentiate from other Pharma/ Biotech companies
Nice to have
• simplicity/ minimalist logo vivid colors gradient 3D Life-Sciences inspired Simple geometry Balance
Should not have
• mascot/ emblem watermark logo animated ink style nature-inspired inventive typography artistic chaos

```html
<!DOCTYPE html>
<html lang="en">
<head>
<meta charset="utf-8">
<title>Corvane Therapeutics – Presentation Template</title>
<link href="https://fonts.googleapis.com/css2?family=Outfit:wght@300;400;500;600;700&display=swap" rel="stylesheet">
<style>
  :root{
    --blue:#0054AA;
    --blue-mid:#0677BA;
    --blue-light:#7BADD7;
    --pink:#E54698;
    --magenta:#A7469A;
    --magenta-mid:#B969AE;
    --lilac:#B7A5CE;
    --lilac-soft:#D3A5CF;
    --purple:#6B429C;
    --ink:#4a4a55;
    --page:#d8d9dd;
  }
  *{box-sizing:border-box;margin:0;padding:0}
  html,body{width:675px;height:1200px;overflow:hidden}
  body{background:var(--page);font-family:"Outfit",Arial,sans-serif;position:relative;color:var(--ink)}

  /* hero */
  .hero{position:absolute;left:0;top:0;width:675px;height:434px;background:linear-gradient(180deg,#c6c9d4 0%,#e2e3e8 100%)}
  .hero-brand{position:absolute;left:503px;top:58px;font-size:15px;font-weight:500;color:var(--blue);line-height:1;display:flex;align-items:center;gap:7px;white-space:nowrap}
  .hero-brand i{display:block;width:16px;height:16px;background:var(--blue)}
  .swatches{position:absolute;left:503px;top:102px;display:flex;gap:8.5px}
  .swatches span{width:13px;height:13px;border-radius:50%}
  .hero-cell{position:absolute;left:108px;top:96px;width:362px;height:204px;overflow:hidden;box-shadow:0 14px 34px rgba(40,40,70,.3)}
  .hero-cell .slide{transform:scale(.8)}

  /* grid cells */
  .cell{position:absolute;width:210px;height:118px;overflow:hidden}
  .c1{left:15px}.c2{left:232px}.c3{left:450px}
  .r1{top:434px}.r2{top:560px}.r3{top:685px}.r4{top:810px}.r5{top:936px}.r6{top:1065px}

  .slide{position:absolute;left:0;top:0;width:452px;height:254px;background:#fff;overflow:hidden;transform:scale(.4646);transform-origin:0 0}
  .art{position:absolute;left:0;top:0;width:452px;height:254px}

  /* brand lockup */
  .brand{position:absolute;font-weight:500;color:var(--blue);display:flex;align-items:center;gap:4px;line-height:1;font-size:11px;right:22px;top:25px}
  .brand i{display:block;width:11px;height:11px;background:var(--blue)}
  .brand.light{color:#fff}.brand.light i{background:#fff}
  .brand.lg{font-size:13px;left:28px;top:44px;right:auto}
  .brand.lg i{width:13px;height:13px}

  /* title slides */
  .t-name{position:absolute;left:28px;top:98px;font-size:25px;font-weight:700;line-height:1.02;color:var(--blue)}
  .t-name span{display:block;color:var(--magenta-mid)}
  .t-date{position:absolute;left:28px;top:160px;font-size:6px;color:var(--ink)}
  .t-copy{position:absolute;left:28px;top:204px;font-size:5px;color:#aaa}
  .dark .t-name,.blue-bg .t-name{color:#fff}
  .dark .t-name span{color:var(--magenta-mid)}
  .blue-bg .t-name span{color:#fff}
  .dark .t-date,.dark .t-copy,.blue-bg .t-date,.blue-bg .t-copy{color:#fff}
  .dark{background:#000}.blue-bg{background:var(--blue)}

  /* content slides */
  .s-title{position:absolute;left:24px;top:17px;font-size:18px;font-weight:400;color:var(--blue)}
  .s-title span{color:var(--magenta-mid)}
  .foot{position:absolute;left:8px;top:235px;width:436px;height:8px;border-radius:4px;background:linear-gradient(90deg,var(--blue),var(--purple) 50%,var(--magenta-mid))}
  .foot em{position:absolute;left:6px;top:1.3px;font-style:normal;font-size:4.5px;color:#fff;font-weight:600}
  .foot b{position:absolute;right:6px;top:0;height:8px;width:20px;border-radius:4px;background:var(--blue);color:#fff;font-size:5px;text-align:center;line-height:8px}

  .p{position:absolute;font-size:6.5px;line-height:1.25;color:var(--ink)}
  .p.c{text-align:center}
  .h{position:absolute;font-size:9px;font-weight:500;line-height:1.1}
  .bl{position:absolute;font-size:6.5px;line-height:1.25;color:var(--ink);list-style:none}
  .bl li{position:relative;padding-left:9px;margin-bottom:4px}
  .bl li::before{content:"";position:absolute;left:1px;top:2.5px;width:3px;height:3px;border-radius:50%;background:var(--blue)}
  .bl.tick li{margin-bottom:1px;padding-left:8px}
  .bl.tick li::before{content:"✓";background:none;width:auto;height:auto;top:0;color:var(--blue);font-size:5.5px}

  .photo{position:absolute}
  .ph-lab{background:radial-gradient(circle at 35% 45%,#f2f5f9 0%,#a9c0d8 30%,#3f6e9e 70%,#22436b 100%)}
  .ph-clinic{background:radial-gradient(circle at 60% 40%,#fbf7f9 0%,#e3d3df 40%,#b8a6c2 75%,#8e86a6 100%)}
  .ph-tablet{background:radial-gradient(circle at 55% 55%,#eef2f6 0%,#b9c9d9 35%,#6e8bab 75%,#3f5a7c 100%)}

  .blue{color:var(--blue)}.mag{color:var(--magenta-mid)}.lil{color:var(--lilac)}.pnk{color:var(--pink)}.lbl{color:var(--blue-light)}.pur{color:var(--purple)}

  .num{position:absolute;font-size:16px;color:#c8c8cf;font-weight:300;line-height:1}

  .avatar{position:absolute;width:56px;height:56px;border-radius:50%;background:radial-gradient(circle at 50% 40%,#e9e4df 0%,#b9b2ab 50%,#5f646e 100%)}

  .dot{position:absolute;border-radius:50%;color:#fff;text-align:center;font-weight:500}

  /* contact slides */
  .contact .c-head{position:absolute;left:44px;top:160px;font-size:12px;color:#fff}
  .contact .c-line{position:absolute;left:44px;font-size:6px;color:#fff}
  .contact .c-row{position:absolute;left:44px;font-size:6px;color:#fff;display:flex;align-items:center;gap:5px}
  .contact .c-row svg{width:7px;height:7px}
  .contact .c-copy{position:absolute;left:180px;top:240px;font-size:4.5px;color:#ddd}
</style>
</head>
<body>

<svg width="0" height="0" style="position:absolute">
  <defs>
    <linearGradient id="phA" x1="0" y1="0" x2="1" y2="1"><stop offset="0" stop-color="#f1ecef"/><stop offset=".35" stop-color="#d9c9d6"/><stop offset=".6" stop-color="#9fb6cc"/><stop offset="1" stop-color="#e6e1e9"/></linearGradient>
    <linearGradient id="phB" x1="0" y1="0" x2="1" y2="1"><stop offset="0" stop-color="#e7edf4"/><stop offset=".45" stop-color="#5d86b0"/><stop offset=".75" stop-color="#2b4f7d"/><stop offset="1" stop-color="#b9c9da"/></linearGradient>
    <linearGradient id="phC" x1="0" y1="0" x2="1" y2="1"><stop offset="0" stop-color="#6f8fb2"/><stop offset=".5" stop-color="#d4dde8"/><stop offset="1" stop-color="#3d6592"/></linearGradient>
    <linearGradient id="bld" x1="0" y1="0" x2="1" y2="1"><stop offset="0" stop-color="#0d1322"/><stop offset=".6" stop-color="#3d4f6c"/><stop offset="1" stop-color="#1e2a40"/></linearGradient>
    <linearGradient id="bldP" x1="0" y1="0" x2="1" y2="1"><stop offset="0" stop-color="#2b1a38"/><stop offset=".6" stop-color="#5c3d6e"/><stop offset="1" stop-color="#1c1226"/></linearGradient>
    <linearGradient id="bldK" x1="0" y1="0" x2="1" y2="1"><stop offset="0" stop-color="#050506"/><stop offset=".65" stop-color="#3a3d48"/><stop offset="1" stop-color="#1a1a1e"/></linearGradient>
  </defs>
</svg>

<!-- HERO -->
<section class="hero">
  <div class="hero-brand"><i></i>Corvane Therapeutics</div>
  <div class="swatches">
    <span style="background:var(--blue)"></span><span style="background:var(--magenta-mid)"></span><span style="background:var(--lilac)"></span><span style="background:var(--pink)"></span><span style="background:var(--blue-light)"></span><span style="background:var(--purple)"></span>
  </div>
  <div class="hero-cell">
    <div class="slide">
      <svg class="art" viewBox="0 0 452 254">
        <polygon role="img" aria-label="Photo of a scientist in a mask reviewing notes in a pharmacy" points="115,0 452,0 452,254 140,254 270,127" fill="url(#phA)"/>
        <polygon points="115,0 240,0 270,127" fill="#B969AE" opacity=".85"/>
        <polygon points="240,0 330,0 270,127" fill="#D3A5CF" opacity=".55"/>
        <polygon points="270,127 140,254 260,254" fill="#0054AA" opacity=".9"/>
      </svg>
      <div class="brand lg"><i></i>Corvane Therapeutics</div>
      <div class="t-name">Corvane<span>Therapeutics</span></div>
      <div class="t-date">Monday, January 17, 2022</div>
      <div class="t-copy">© 2021 Corvane Therapeutics. All Rights Reserved.</div>
    </div>
  </div>
</section>

<!-- ROW 1 : title slides -->
<div class="cell c1 r1"><div class="slide">
  <svg class="art" viewBox="0 0 452 254">
    <polygon role="img" aria-label="Photo of a scientist in a mask in a pharmacy" points="115,0 452,0 452,254 140,254 270,127" fill="url(#phA)"/>
    <polygon points="115,0 240,0 270,127" fill="#B969AE" opacity=".85"/>
    <polygon points="240,0 330,0 270,127" fill="#D3A5CF" opacity=".55"/>
    <polygon points="270,127 140,254 260,254" fill="#0054AA" opacity=".9"/>
  </svg>
  <div class="brand lg"><i></i>Corvane Therapeutics</div>
  <div class="t-name">Corvane<span>Therapeutics</span></div>
  <div class="t-date">Monday, January 17, 2022</div>
  <div class="t-copy">© 2021 Corvane Therapeutics. All Rights Reserved.</div>
</div></div>

<div class="cell c2 r1"><div class="slide dark">
  <svg class="art" viewBox="0 0 452 254">
    <polygon role="img" aria-label="Photo of researchers working in a laboratory" points="115,0 452,0 452,254 140,254 270,127" fill="url(#phB)"/>
    <polygon points="115,0 240,0 270,127" fill="#B969AE" opacity=".85"/>
    <polygon points="240,0 330,0 270,127" fill="#D3A5CF" opacity=".55"/>
    <polygon points="270,127 140,254 260,254" fill="#0054AA" opacity=".9"/>
  </svg>
  <div class="brand lg light"><i></i>Corvane Therapeutics</div>
  <div class="t-name">Corvane<span>Therapeutics</span></div>
  <div class="t-date">Monday, January 17, 2022</div>
  <div class="t-copy">© 2021 Corvane Therapeutics. All Rights Reserved.</div>
</div></div>

<div class="cell c3 r1"><div class="slide blue-bg">
  <svg class="art" viewBox="0 0 452 254">
    <polygon role="img" aria-label="Photo of hands using a tablet" points="115,0 452,0 452,254 140,254 270,127" fill="url(#phC)"/>
    <polygon points="115,0 240,0 270,127" fill="#B969AE" opacity=".85"/>
    <polygon points="240,0 330,0 270,127" fill="#D3A5CF" opacity=".55"/>
    <polygon points="270,127 140,254 260,254" fill="#0054AA" opacity=".9"/>
  </svg>
  <div class="brand lg light"><i></i>Corvane Therapeutics</div>
  <div class="t-name">Corvane<span>Therapeutics</span></div>
  <div class="t-date">Monday, January 17, 2022</div>
  <div class="t-copy">© 2021 Corvane Therapeutics. All Rights Reserved.</div>
</div></div>

<!-- ROW 2 -->
<div class="cell c1 r2"><div class="slide">
  <div class="s-title">Agenda <span>Slide</span></div>
  <div class="brand"><i></i>Corvane</div>
  <div class="num" style="left:62px;top:82px">1</div><div class="h blue" style="left:84px;top:76px">Title Goes Here</div><div class="p" style="left:84px;top:88px;width:140px">Short text about this agenda item, kept brief and clear.</div>
  <div class="num" style="left:240px;top:82px">2</div><div class="h mag" style="left:262px;top:76px">Title Goes Here</div><div class="p" style="left:262px;top:88px;width:140px">Short text about this agenda item, kept brief and clear.</div>
  <div class="num" style="left:62px;top:126px">3</div><div class="h mag" style="left:84px;top:120px">Title Goes Here</div><div class="p" style="left:84px;top:132px;width:140px">Short text about this agenda item, kept brief and clear.</div>
  <div class="num" style="left:240px;top:126px">4</div><div class="h blue" style="left:262px;top:120px">Title Goes Here</div><div class="p" style="left:262px;top:132px;width:140px">Short text about this agenda item, kept brief and clear.</div>
  <div class="num" style="left:62px;top:170px">5</div><div class="h blue" style="left:84px;top:164px">Title Goes Here</div><div class="p" style="left:84px;top:176px;width:140px">Short text about this agenda item, kept brief and clear.</div>
  <div class="num" style="left:240px;top:170px">6</div><div class="h mag" style="left:262px;top:164px">Title Goes Here</div><div class="p" style="left:262px;top:176px;width:140px">Short text about this agenda item, kept brief and clear.</div>
  <div class="foot"><em>© 2021 Corvane Therapeutics. All Rights Reserved.</em><b>4</b></div>
</div></div>

<div class="cell c2 r2"><div class="slide">
  <div class="photo ph-lab" role="img" aria-label="Photo of a researcher at a lab bench" style="left:28px;top:0;width:210px;height:136px"></div>
  <div class="photo ph-tablet" role="img" aria-label="Photo of hands holding a tablet" style="left:28px;top:140px;width:103px;height:70px"></div>
  <div class="photo ph-clinic" role="img" aria-label="Photo of a scientist in a pharmacy" style="left:135px;top:140px;width:103px;height:70px"></div>
  <div class="brand"><i></i>Corvane</div>
  <div class="s-title" style="left:256px;top:58px">About <span>Us</span></div>
  <div class="p" style="left:256px;top:84px;width:172px">We combine genetics, data and care to find new ways to prevent and treat disorders of aging for older patients.</div>
  <ul class="bl" style="left:256px;top:118px;width:172px">
    <li>Shift from disease management to prevention.</li>
    <li>Focus on longer health span, not only life span.</li>
    <li>Multidisciplinary research teams and open trials.</li>
    <li>Care and attention for every elderly patient.</li>
  </ul>
  <div class="foot"><em>© 2021 Corvane Therapeutics. All Rights Reserved.</em><b>5</b></div>
</div></div>

<div class="cell c3 r2"><div class="slide">
  <div class="s-title">Meet Our <span>Team</span></div>
  <div class="brand"><i></i>Corvane</div>
  <div class="avatar" role="img" aria-label="Team member portrait" style="left:62px;top:68px"></div>
  <div class="avatar" role="img" aria-label="Team member portrait" style="left:198px;top:68px"></div>
  <div class="avatar" role="img" aria-label="Team member portrait" style="left:334px;top:68px"></div>
  <div class="h blue" style="left:30px;top:131px;width:120px;text-align:center">Name Goes Here</div>
  <div class="h mag" style="left:166px;top:131px;width:120px;text-align:center">Name Goes Here</div>
  <div class="h lil" style="left:302px;top:131px;width:120px;text-align:center">Name Goes Here</div>
  <div class="p c" style="left:30px;top:143px;width:120px">Job Title Goes Here</div>
  <div class="p c" style="left:166px;top:143px;width:120px">Job Title Goes Here</div>
  <div class="p c" style="left:302px;top:143px;width:120px">Job Title Goes Here</div>
  <div class="p c" style="left:32px;top:157px;width:116px">A short note on this person, their focus and their role in the team.</div>
  <div class="p c" style="left:168px;top:157px;width:116px">A short note on this person, their focus and their role in the team.</div>
  <div class="p c" style="left:304px;top:157px;width:116px">A short note on this person, their focus and their role in the team.</div>
  <div class="foot"><em>© 2021 Corvane Therapeutics. All Rights Reserved.</em><b>6</b></div>
</div></div>

<!-- ROW 3 -->
<div class="cell c1 r3"><div class="slide">
  <div class="s-title">Slide Title <span>Goes Here</span></div>
  <div class="brand"><i></i>Corvane</div>
  <ul class="bl" style="left:24px;top:50px;width:210px">
    <li>Brief point on the research goal and the method we use to reach it.</li>
    <li>Brief point on early results and what they show for our patients.</li>
    <li>Brief point on next steps and the partners joining the work.</li>
  </ul>
  <div style="position:absolute;left:0;top:132px;width:452px;height:66px;background:linear-gradient(90deg,var(--blue) 55%,var(--purple) 85%,var(--magenta-mid))"></div>
  <div class="photo ph-lab" role="img" aria-label="Photo of a scientist looking at a screen" style="left:253px;top:55px;width:162px;height:77px"></div>
  <div class="photo" style="left:253px;top:198px;width:162px;height:14px;background:#5d7fa6"></div>
  <div class="p" style="left:40px;top:140px;width:372px;color:#fff">Our work joins genetics, clinical care and data science to move from treating disease late to preventing it early. We test ideas quickly, share results openly and keep patients at the center of every study we run together with our partners.</div>
  <div class="foot"><em>© 2021 Corvane Therapeutics. All Rights Reserved.</em><b>7</b></div>
</div></div>

<div class="cell c2 r3"><div class="slide">
  <div class="s-title">Slide Title <span>Goes Here</span></div>
  <div class="brand"><i></i>Corvane</div>
  <div class="p c" style="left:50px;top:50px;width:352px">A short introduction to the four areas below, explaining how each one supports our aim of longer and healthier lives for older patients.</div>
  <svg class="art" viewBox="0 0 452 254">
    <circle cx="70" cy="97" r="14" fill="#0054AA"/><circle cx="164" cy="97" r="14" fill="#B969AE"/><circle cx="258" cy="97" r="14" fill="#B7A5CE"/><circle cx="352" cy="97" r="14" fill="#E54698"/>
    <path d="M63 97h14M66 93l8 8M74 93l-8 8" stroke="#fff" stroke-width="1.5"/>
    <path d="M157 96h14a7 7 0 0 1-14 0z" fill="#fff"/>
    <path d="M255 104h8M259 104v-10l4-3" stroke="#fff" stroke-width="1.5" fill="none"/>
    <path d="M349 90h6M350 90v5l-4 9h12l-4-9v-5" stroke="#fff" stroke-width="1.4" fill="none"/>
  </svg>
  <div class="h blue" style="left:25px;top:116px;width:90px;text-align:center">Heading</div>
  <div class="h mag" style="left:119px;top:116px;width:90px;text-align:center">Heading</div>
  <div class="h lil" style="left:213px;top:116px;width:90px;text-align:center">Heading</div>
  <div class="h pnk" style="left:307px;top:116px;width:90px;text-align:center">Heading</div>
  <div class="p c" style="left:25px;top:129px;width:90px">Short text on this area of our work and why it matters to patients.</div>
  <div class="p c" style="left:119px;top:129px;width:90px">Short text on this area of our work and why it matters to patients.</div>
  <div class="p c" style="left:213px;top:129px;width:90px">Short text on this area of our work and why it matters to patients.</div>
  <div class="p c" style="left:307px;top:129px;width:90px">Short text on this area of our work and why it matters to patients.</div>
  <div class="foot"><em>© 2021 Corvane Therapeutics. All Rights Reserved.</em><b>8</b></div>
</div></div>

<div class="cell c3 r3"><div class="slide">
  <div class="s-title">Slide Title <span>Goes Here</span></div>
  <div class="brand"><i></i>Corvane</div>
  <div class="p" style="left:24px;top:48px;width:404px">A short opening paragraph that sets out the topic of this slide and the main finding we want the audience to remember after the talk.</div>
  <div class="p" style="left:24px;top:72px;width:404px">A second paragraph adds context, explains the method and points to the data shown in the panel below.</div>
  <div class="photo ph-lab" role="img" aria-label="Photo of lab equipment and sample tubes" style="left:0;top:112px;width:232px;height:95px"></div>
  <div style="position:absolute;left:232px;top:112px;width:192px;height:95px;background:linear-gradient(90deg,var(--blue),var(--purple) 70%,var(--magenta-mid))"></div>
  <div style="position:absolute;left:246px;top:124px;width:172px;font-size:10px;line-height:1.2;color:#fff">A short statement that sums up the key message of this slide in a few clear words.</div>
  <div class="foot"><em>© 2021 Corvane Therapeutics. All Rights Reserved.</em><b>9</b></div>
</div></div>

<!-- ROW 4 -->
<div class="cell c1 r4"><div class="slide">
  <div class="s-title">Slide Title <span>Goes Here</span></div>
  <div class="brand"><i></i>Corvane</div>
  <div class="h blue" style="left:24px;top:52px">Title Goes Here!</div>
  <div class="h mag" style="left:158px;top:52px">Title Goes Here!</div>
  <div class="h lil" style="left:292px;top:52px">Title Goes Here!</div>
  <div style="position:absolute;left:150px;top:50px;width:.6px;height:150px;background:#ddd"></div>
  <div style="position:absolute;left:284px;top:50px;width:.6px;height:150px;background:#ddd"></div>
  <ul class="bl" style="left:24px;top:68px;width:122px"><li>Brief point on this topic with one clear idea.</li><li>Second point adds a detail or a result.</li><li>Third point names a next step.</li><li>Last point closes it.</li></ul>
  <ul class="bl" style="left:158px;top:68px;width:122px"><li>Brief point on this topic with one clear idea.</li><li>Second point adds a detail or a result.</li><li>Third point names a next step.</li><li>Last point closes it.</li></ul>
  <ul class="bl" style="left:292px;top:68px;width:122px"><li>Brief point on this topic with one clear idea.</li><li>Second point adds a detail or a result.</li><li>Third point names a next step.</li><li>Last point closes it.</li></ul>
  <div class="foot"><em>© 2021 Corvane Therapeutics. All Rights Reserved.</em><b>10</b></div>
</div></div>

<div class="cell c2 r4"><div class="slide">
  <div class="s-title">Slide Title <span>Goes Here</span></div>
  <div class="brand"><i></i>Corvane</div>
  <div class="dot" style="left:43px;top:141px;width:18px;height:18px;line-height:18px;font-size:10px;background:var(--blue)">1</div>
  <div class="dot" style="left:112px;top:141px;width:18px;height:18px;line-height:18px;font-size:10px;background:var(--magenta-mid)">2</div>
  <div class="dot" style="left:181px;top:141px;width:18px;height:18px;line-height:18px;font-size:10px;background:var(--lilac)">3</div>
  <div class="dot" style="left:251px;top:141px;width:18px;height:18px;line-height:18px;font-size:10px;background:var(--pink)">4</div>
  <div class="dot" style="left:320px;top:141px;width:18px;height:18px;line-height:18px;font-size:10px;background:var(--blue-light)">5</div>
  <div class="dot" style="left:389px;top:141px;width:18px;height:18px;line-height:18px;font-size:10px;background:var(--purple)">6</div>
  <ul class="bl tick" style="left:100px;top:76px;width:62px;font-size:5.5px"><li>Short step note.</li><li>Brief detail here.</li></ul>
  <ul class="bl tick" style="left:239px;top:76px;width:62px;font-size:5.5px"><li>Short step note.</li><li>Brief detail here.</li></ul>
  <ul class="bl tick" style="left:377px;top:76px;width:62px;font-size:5.5px"><li>Short step note.</li><li>Brief detail here.</li></ul>
  <div class="h mag" style="left:91px;top:116px;width:60px;text-align:center;font-size:7px">Heading<br>Goes Here!</div>
  <div class="h pnk" style="left:230px;top:116px;width:60px;text-align:center;font-size:7px">Heading<br>Goes Here!</div>
  <div class="h pur" style="left:368px;top:116px;width:60px;text-align:center;font-size:7px">Heading<br>Goes Here!</div>
  <div class="h blue" style="left:22px;top:164px;width:60px;text-align:center;font-size:7px">Heading<br>Goes Here!</div>
  <div class="h lil" style="left:160px;top:164px;width:60px;text-align:center;font-size:7px">Heading<br>Goes Here!</div>
  <div class="h lbl" style="left:299px;top:164px;width:60px;text-align:center;font-size:7px">Heading<br>Goes Here!</div>
  <ul class="bl tick" style="left:30px;top:184px;width:62px;font-size:5.5px"><li>Short step note.</li><li>Brief detail here.</li></ul>
  <ul class="bl tick" style="left:168px;top:184px;width:62px;font-size:5.5px"><li>Short step note.</li><li>Brief detail here.</li></ul>
  <ul class="bl tick" style="left:307px;top:184px;width:62px;font-size:5.5px"><li>Short step note.</li><li>Brief detail here.</li></ul>
  <div class="foot"><em>© 2021 Corvane Therapeutics. All Rights Reserved.</em><b>11</b></div>
</div></div>

<div class="cell c3 r4"><div class="slide">
  <div class="s-title">Column <span>Chart Slide</span></div>
  <div class="brand"><i></i>Corvane</div>
  <svg class="art" viewBox="0 0 452 254" font-family="Outfit, sans-serif">
    <g font-size="5" fill="#777">
      <text x="22" y="59">6</text><text x="22" y="82">5</text><text x="22" y="105">4</text><text x="22" y="128">3</text><text x="22" y="151">2</text><text x="22" y="174">1</text><text x="22" y="197">0</text>
    </g>
    <rect x="40" y="113" width="7" height="80" fill="#0054AA"/><rect x="48" y="140" width="7" height="53" fill="#B969AE"/><rect x="56" y="147" width="7" height="46" fill="#B7A5CE"/>
    <rect x="88" y="147" width="7" height="46" fill="#0054AA"/><rect x="96" y="111" width="7" height="82" fill="#B969AE"/><rect x="104" y="147" width="7" height="46" fill="#B7A5CE"/>
    <rect x="136" y="129" width="7" height="64" fill="#0054AA"/><rect x="144" y="155" width="7" height="38" fill="#B969AE"/><rect x="152" y="140" width="7" height="53" fill="#B7A5CE"/>
    <rect x="184" y="110" width="7" height="83" fill="#0054AA"/><rect x="192" y="140" width="7" height="53" fill="#B969AE"/><rect x="200" y="93" width="7" height="100" fill="#B7A5CE"/>
    <line x1="32" y1="193" x2="220" y2="193" stroke="#ccc" stroke-width=".6"/>
    <g font-size="4.5" fill="#666" text-anchor="middle"><text x="51" y="201">Kategorie 1</text><text x="99" y="201">Kategorie 2</text><text x="147" y="201">Kategorie 3</text><text x="195" y="201">Kategorie 4</text></g>
    <g font-size="4.5" fill="#666"><rect x="88" y="206" width="3" height="3" fill="#0054AA"/><text x="92" y="209">Serie 1</text><rect x="110" y="206" width="3" height="3" fill="#B969AE"/><text x="114" y="209">Serie 2</text><rect x="132" y="206" width="3" height="3" fill="#B7A5CE"/><text x="136" y="209">Serie 3</text></g>
    <rect x="257" y="57" width="8" height="8" fill="#0054AA"/><rect x="257" y="105" width="8" height="8" fill="#B969AE"/><rect x="257" y="153" width="8" height="8" fill="#B7A5CE"/>
  </svg>
  <div class="h blue" style="left:271px;top:56px">Title Goes Here!</div>
  <div class="p" style="left:271px;top:68px;width:150px;font-size:6px">Short note on this data series and what the numbers show.</div>
  <div class="h mag" style="left:271px;top:104px">Title Goes Here!</div>
  <div class="p" style="left:271px;top:116px;width:150px;font-size:6px">Short note on this data series and what the numbers show.</div>
  <div class="h lil" style="left:271px;top:152px">Title Goes Here!</div>
  <div class="p" style="left:271px;top:164px;width:150px;font-size:6px">Short note on this data series and what the numbers show.</div>
  <div class="foot"><em>© 2021 Corvane Therapeutics. All Rights Reserved.</em><b>12</b></div>
</div></div>

<!-- ROW 5 -->
<div class="cell c1 r5"><div class="slide">
  <div class="s-title">Pie <span>Chart Slide</span></div>
  <div class="brand"><i></i>Corvane</div>
  <svg class="art" viewBox="0 0 452 254" font-family="Outfit, sans-serif">
    <rect x="12" y="72" width="140" height="46" fill="#f5f5f7"/><rect x="12" y="126" width="140" height="46" fill="#f5f5f7"/>
    <rect x="300" y="72" width="140" height="46" fill="#f5f5f7"/><rect x="300" y="126" width="140" height="46" fill="#f5f5f7"/>
    <rect x="0" y="72" width="18" height="46" fill="#E54698"/><rect x="0" y="126" width="18" height="46" fill="#B7A5CE"/>
    <rect x="434" y="72" width="18" height="46" fill="#0054AA"/><rect x="434" y="126" width="18" height="46" fill="#B969AE"/>
    <g font-size="8" fill="#fff" text-anchor="middle">
      <text transform="translate(12 95) rotate(-90)">20%</text><text transform="translate(12 149) rotate(-90)">40%</text>
      <text transform="translate(444 95) rotate(-90)">80%</text><text transform="translate(444 149) rotate(-90)">60%</text>
    </g>
    <path d="M226 62A68 68 0 0 1 226 198L226 130Z" fill="#0054AA"/>
    <path d="M226 198A68 68 0 0 1 160.3 147.6L226 130Z" fill="#B969AE"/>
    <path d="M160.3 147.6A68 68 0 0 1 187 74.3L226 130Z" fill="#B7A5CE"/>
    <path d="M187 74.3A68 68 0 0 1 226 62L226 130Z" fill="#E54698"/>
    <g font-size="6.5" fill="#fff" text-anchor="middle"><text x="266" y="132">80%</text><text x="196" y="186">60%</text><text x="178" y="117">40%</text><text x="211" y="76">20%</text></g>
  </svg>
  <div class="h mag" style="left:34px;top:78px;width:112px;text-align:center">Heading</div>
  <div class="p c" style="left:34px;top:90px;width:112px;font-size:6px">Short note on this share of the total result.</div>
  <div class="h mag" style="left:34px;top:132px;width:112px;text-align:center">Heading</div>
  <div class="p c" style="left:34px;top:144px;width:112px;font-size:6px">Short note on this share of the total result.</div>
  <div class="h mag" style="left:308px;top:78px;width:112px;text-align:center">Heading</div>
  <div class="p c" style="left:308px;top:90px;width:112px;font-size:6px">Short note on this share of the total result.</div>
  <div class="h mag" style="left:308px;top:132px;width:112px;text-align:center">Heading</div>
  <div class="p c" style="left:308px;top:144px;width:112px;font-size:6px">Short note on this share of the total result.</div>
  <div class="foot"><em>© 2021 Corvane Therapeutics. All Rights Reserved.</em><b>13</b></div>
</div></div>

<div class="cell c2 r5"><div class="slide">
  <div class="s-title">Table <span>Slide</span></div>
  <div class="brand"><i></i>Corvane</div>
  <svg class="art" viewBox="0 0 452 254" font-family="Outfit, sans-serif">
    <rect x="16" y="50" width="104" height="46" fill="#0054AA"/>
    <rect x="120" y="50" width="104" height="38" fill="#B969AE"/><rect x="224" y="50" width="104" height="38" fill="#B7A5CE"/><rect x="328" y="50" width="104" height="38" fill="#E54698"/>
    <rect x="120" y="88" width="104" height="8" fill="#c882bf"/><rect x="224" y="88" width="104" height="8" fill="#c6b8da"/><rect x="328" y="88" width="104" height="8" fill="#ec6aae"/>
    <line x1="120" y1="61" x2="432" y2="61" stroke="#fff" stroke-width=".5" opacity=".6"/>
    <text x="22" y="70" font-size="11" fill="#fff">Title Goes</text><text x="22" y="84" font-size="11" fill="#fff">Here!</text>
    <g font-size="5.5" fill="#fff" text-anchor="middle"><text x="172" y="58">Heading 1</text><text x="276" y="58">Heading 2</text><text x="380" y="58">Heading 3</text></g>
    <g font-size="4.5" fill="#fff" text-anchor="middle"><text x="172" y="93.5">Text Goes Here</text><text x="276" y="93.5">Text Goes Here</text><text x="380" y="93.5">Text Goes Here</text></g>
    <g font-size="12" fill="#fff" text-anchor="middle"><text x="172" y="81">2019</text><text x="276" y="81">2020</text><text x="380" y="81">2021</text></g>
    <g font-size="5.5" fill="#444">
      <text x="18" y="106">Text Goes Here</text><text x="18" y="119">Text Goes Here</text><text x="18" y="132">Text Goes Here</text><text x="18" y="145">Text Goes Here</text><text x="18" y="158">Text Goes Here</text>
    </g>
    <g stroke="#e4e4ea" stroke-width=".5"><line x1="16" y1="110" x2="432" y2="110"/><line x1="16" y1="123" x2="432" y2="123"/><line x1="16" y1="136" x2="432" y2="136"/><line x1="16" y1="149" x2="432" y2="149"/></g>
    <g font-size="6" text-anchor="middle">
      <text x="172" y="106" fill="#B969AE">✓</text><text x="276" y="106" fill="#B7A5CE">✓</text><text x="380" y="106" fill="#E54698">✓</text>
      <text x="172" y="119" fill="#B969AE">✓</text><text x="276" y="119" fill="#B7A5CE">✓</text><text x="380" y="119" fill="#E54698">✓</text>
      <text x="172" y="132" fill="#B969AE">✓</text><text x="276" y="132" fill="#B7A5CE">✓</text><text x="380" y="132" fill="#E54698">✓</text>
      <text x="276" y="145" fill="#B7A5CE">✓</text><text x="380" y="145" fill="#E54698">✓</text>
      <text x="380" y="158" fill="#E54698">✓</text>
    </g>
    <rect x="16" y="163" width="104" height="9" fill="#0054AA"/><rect x="120" y="163" width="104" height="9" fill="#B969AE"/><rect x="224" y="163" width="104" height="9" fill="#B7A5CE"/><rect x="328" y="163" width="104" height="9" fill="#E54698"/>
    <g font-size="4.5" fill="#fff" text-anchor="middle"><text x="172" y="169">Text Goes Here</text><text x="276" y="169">Text Goes Here</text><text x="380" y="169">Text Goes Here</text></g>
  </svg>
  <div class="foot"><em>© 2021 Corvane Therapeutics. All Rights Reserved.</em><b>14</b></div>
</div></div>

<div class="cell c3 r5"><div class="slide">
  <div class="s-title">Slide Title <span>Goes Here</span></div>
  <div class="brand"><i></i>Corvane</div>
  <div class="photo ph-tablet" role="img" aria-label="Photo of a hand using a tablet" style="left:0;top:48px;width:150px;height:152px"></div>
  <div style="position:absolute;left:160px;top:48px;width:142px;height:152px;background:var(--blue)"></div>
  <div style="position:absolute;left:312px;top:48px;width:140px;height:152px;background:var(--magenta-mid)"></div>
  <div style="position:absolute;left:172px;top:52px;font-size:30px;font-weight:700;color:#fff;line-height:1">“</div>
  <div style="position:absolute;left:324px;top:52px;font-size:30px;font-weight:700;color:#fff;line-height:1">“</div>
  <div class="p" style="left:172px;top:104px;width:118px;color:#fff;font-size:8px">A short quote from a partner or patient about our work and the care we bring to it every day.</div>
  <div class="p" style="left:324px;top:104px;width:118px;color:#fff;font-size:8px">A short quote from a partner or patient about our work and the care we bring to it every day.</div>
  <div class="foot"><em>© 2021 Corvane Therapeutics. All Rights Reserved.</em><b>15</b></div>
</div></div>

<!-- ROW 6 : contact slides -->
<div class="cell c1 r6"><div class="slide contact" style="background:#0b0d18">
  <svg class="art" viewBox="0 0 452 254">
    <rect role="img" aria-label="Photo of a modern glass office building" x="0" y="0" width="452" height="254" fill="url(#bld)"/>
    <polygon points="180,0 452,0 452,120" fill="#B969AE" opacity=".6"/>
    <polygon points="230,254 452,110 452,254" fill="#0054AA" opacity=".55"/>
  </svg>
  <div class="brand lg light" style="left:44px;top:100px"><i></i>Corvane Therapeutics</div>
  <div class="c-head">Contact Us</div>
  <div class="c-line" style="top:178px">Insert Company Address Here!</div>
  <div class="c-row" style="top:191px"><svg viewBox="0 0 10 10"><path d="M2 1l2 0 1 2.5-1.3 1a5 5 0 0 0 2.8 2.8l1-1.3L10 7v2a1 1 0 0 1-1 1A8 8 0 0 1 1 2a1 1 0 0 1 1-1z" fill="#fff"/></svg>Insert Phone Number</div>
  <div class="c-row" style="top:201px"><svg viewBox="0 0 10 10"><circle cx="5" cy="5" r="4" fill="none" stroke="#fff"/><circle cx="5" cy="5" r="1.5" fill="#fff"/></svg>Insert E-Mail Address</div>
  <div class="c-row" style="top:211px"><svg viewBox="0 0 10 10"><circle cx="5" cy="5" r="4" fill="none" stroke="#fff"/><path d="M1 5h8M5 1v8" stroke="#fff" stroke-width=".7"/></svg>Insert URL Address</div>
  <div class="c-copy">© 2021 Corvane Therapeutics. All Rights Reserved.</div>
</div></div>

<div class="cell c2 r6"><div class="slide contact" style="background:#1a1024">
  <svg class="art" viewBox="0 0 452 254">
    <rect role="img" aria-label="Photo of a modern glass office building" x="0" y="0" width="452" height="254" fill="url(#bldP)"/>
    <polygon points="180,0 452,0 452,120" fill="#B969AE" opacity=".6"/>
    <polygon points="230,254 452,110 452,254" fill="#0054AA" opacity=".55"/>
  </svg>
  <div class="brand lg light" style="left:44px;top:100px"><i></i>Corvane Therapeutics</div>
  <div class="c-head">Contact Us</div>
  <div class="c-line" style="top:178px">Insert Company Address Here!</div>
  <div class="c-row" style="top:191px"><svg viewBox="0 0 10 10"><path d="M2 1l2 0 1 2.5-1.3 1a5 5 0 0 0 2.8 2.8l1-1.3L10 7v2a1 1 0 0 1-1 1A8 8 0 0 1 1 2a1 1 0 0 1 1-1z" fill="#fff"/></svg>Insert Phone Number</div>
  <div class="c-row" style="top:201px"><svg viewBox="0 0 10 10"><circle cx="5" cy="5" r="4" fill="none" stroke="#fff"/><circle cx="5" cy="5" r="1.5" fill="#fff"/></svg>Insert E-Mail Address</div>
  <div class="c-row" style="top:211px"><svg viewBox="0 0 10 10"><circle cx="5" cy="5" r="4" fill="none" stroke="#fff"/><path d="M1 5h8M5 1v8" stroke="#fff" stroke-width=".7"/></svg>Insert URL Address</div>
  <div class="c-copy">© 2021 Corvane Therapeutics. All Rights Reserved.</div>
</div></div>

<div class="cell c3 r6"><div class="slide contact" style="background:#050505">
  <svg class="art" viewBox="0 0 452 254">
    <rect role="img" aria-label="Photo of a modern glass office building" x="0" y="0" width="452" height="254" fill="url(#bldK)"/>
    <polygon points="180,0 452,0 452,120" fill="#B969AE" opacity=".6"/>
    <polygon points="230,254 452,110 452,254" fill="#0054AA" opacity=".55"/>
  </svg>
  <div class="brand lg light" style="left:44px;top:100px"><i></i>Corvane Therapeutics</div>
  <div class="c-head">Contact Us</div>
  <div class="c-line" style="top:178px">Insert Company Address Here!</div>
  <div class="c-row" style="top:191px"><svg viewBox="0 0 10 10"><path d="M2 1l2 0 1 2.5-1.3 1a5 5 0 0 0 2.8 2.8l1-1.3L10 7v2a1 1 0 0 1-1 1A8 8 0 0 1 1 2a1 1 0 0 1 1-1z" fill="#fff"/></svg>Insert Phone Number</div>
  <div class="c-row" style="top:201px"><svg viewBox="0 0 10 10"><circle cx="5" cy="5" r="4" fill="none" stroke="#fff"/><circle cx="5" cy="5" r="1.5" fill="#fff"/></svg>Insert E-Mail Address</div>
  <div class="c-row" style="top:211px"><svg viewBox="0 0 10 10"><circle cx="5" cy="5" r="4" fill="none" stroke="#fff"/><path d="M1 5h8M5 1v8" stroke="#fff" stroke-width=".7"/></svg>Insert URL Address</div>
  <div class="c-copy">© 2021 Corvane Therapeutics. All Rights Reserved.</div>
</div></div>

</body>
</html>
```